Upmarket Dessert Lounge needs a Business Card Design

We are an upmarket dessert lounge needing a business card to match our image.

We want something that is simple yet beautiful, feminine, classy, sophisticated and elegant. We want it to stand out and don't mind if it is bold.

The design should include our logo and colours of red or maroon with gold highlights. We don't mind if black is used.

Marlow & Quince

Target Market(s)

For those who like to indulge or treat themselves and give in to their temptations on good quality desserts.

Industry/Entity Type

Business

Requirements
Must have
• Must include our logo and our name

Marlow & Quince

M & Q

```html
<!DOCTYPE html>
<html lang="en">
<head>
<meta charset="utf-8">
<title>Marlow &amp; Quince – Business Card</title>
<link rel="stylesheet" href="https://fonts.googleapis.com/css2?family=Open+Sans:wght@400;700&display=swap">
<style>
  :root {
    --maroon: #7a1416;
    --gold: #fdd39a;
    --ink: #3a3a3a;
    --card: #ffffff;
    --backdrop: #e4e4e4;
  }
  * { margin: 0; padding: 0; box-sizing: border-box; }
  html, body {
    width: 956px;
    height: 1200px;
    overflow: hidden;
    background: var(--backdrop);
    font-family: "Open Sans", Arial, sans-serif;
    color: var(--ink);
  }
  .canvas { position: relative; width: 956px; height: 1200px; }
  .card {
    position: absolute;
    width: 798px;
    height: 456px;
    background: var(--card);
    border-radius: 30px;
    overflow: hidden;
    box-shadow: 0 6px 14px rgba(0, 0, 0, 0.25);
  }
  .card--front { left: 80px; top: 103px; }
  .card--back { left: 73px; top: 639px; height: 455px; }
  .card__swoosh { position: absolute; left: 0; top: 0; width: 798px; height: 456px; }
  .brand-mark {
    position: absolute;
    left: 0;
    width: 100%;
    text-align: center;
    color: var(--maroon);
    font-weight: 400;
    letter-spacing: 2px;
  }
  .brand-mark--monogram { top: 82px; font-size: 74px; }
  .brand-mark--full { top: 186px; font-size: 54px; }
  .contact {
    position: absolute;
    left: 0;
    width: 100%;
    text-align: center;
  }
  .contact__name { top: 264px; font-size: 21px; }
  .contact__name strong { font-weight: 700; }
  .contact__line { font-size: 18.5px; }
  .contact__line b { font-weight: 700; }
  .contact__phones { top: 319px; }
  .contact__web { top: 354px; }
  .contact__address { top: 393px; }
</style>
</head>
<body>
<main class="canvas">
  <section class="card card--front">
    <svg class="card__swoosh" viewBox="0 0 798 456" aria-hidden="true">
      <path fill="var(--maroon)" d="M545,0 C660,4 750,22 798,58 L798,0 Z"/>
      <path fill="var(--gold)" d="M640,14 C720,22 772,44 798,80 L798,62 C770,36 712,20 640,14 Z"/>
      <path fill="var(--gold)" d="M0,380 C40,410 100,440 170,456 L150,456 C90,440 40,420 0,400 Z"/>
      <path fill="var(--maroon)" d="M0,402 C60,432 150,450 245,456 L0,456 Z"/>
    </svg>
    <div class="brand-mark brand-mark--monogram">M &amp; Q</div>
    <p class="contact contact__name"><strong>Your Name -</strong> Designation</p>
    <p class="contact contact__line contact__phones"><b>p</b> : 123-456-7890 &nbsp;|&nbsp; <b>c</b> : 123-456-7890 &nbsp;|&nbsp; <b>f</b> : 123-456-7890</p>
    <p class="contact contact__line contact__web"><b>e</b> : name@yourwebsite.com &nbsp;|&nbsp; <b>w</b> : www.marlowandquince.com</p>
    <p class="contact contact__line contact__address">0000, Street Name, City Name, Country Code.</p>
  </section>

  <section class="card card--back">
    <div class="brand-mark brand-mark--full">MARLOW &amp; QUINCE</div>
  </section>
</main>
</body>
</html>
```